New Business Card Design

We would like to refresh our business cards and make them look better. We are an IT company specialising in Cloud Services, IT Managed Services, software and hardware. I have attached a PSD of our current design. Also attached our logo.
Updates

I have uploaded all new logos in EPS format.

Can you please edit all designs to include a job title for Marcus Hollis, eg. General Manager

Industry/Entity Type

Software

Colors
ffffff

Requirements
Must have
• Please use white background.
Should not have
• Black background

```html
<!DOCTYPE html>
<html lang="en">
<head>
<meta charset="utf-8">
<title>Meridian Systems – Business Card</title>
<link rel="stylesheet" href="https://fonts.googleapis.com/css2?family=Open+Sans:wght@400;600;700&display=swap">
<style>
  :root {
    --page-bg: #e9eaee;
    --card-white: #ffffff;
    --brand-red: #c13a2a;
    --brand-grey: #878f99;
    --ink: #1e2830;
    --on-dark: #ffffff;
  }
  * { margin: 0; padding: 0; box-sizing: border-box; }
  html, body { width: 1200px; height: 987px; overflow: hidden; }
  body {
    background: var(--page-bg);
    font-family: "Open Sans", Arial, sans-serif;
    position: relative;
  }
  .card {
    position: absolute;
    left: 250px;
    width: 700px;
    height: 400px;
    border-radius: 34px;
    overflow: hidden;
    box-shadow: 0 10px 30px rgba(60, 65, 75, 0.18);
  }
  .card--front { top: 60px; background: var(--card-white); }
  .card--back { top: 527px; background: var(--brand-red); }

  .front-bands { position: absolute; inset: 0; }

  .brand {
    position: absolute;
    left: 58px;
    top: 58px;
    display: flex;
    align-items: center;
    gap: 22px;
  }
  .brand-dot {
    width: 62px; height: 62px;
    border-radius: 50%;
    background: var(--brand-red);
  }
  .brand-name {
    font-size: 44px;
    font-weight: 400;
    letter-spacing: 6px;
    color: var(--ink);
    line-height: 1;
  }

  .person {
    position: absolute;
    left: 150px;
    top: 152px;
    font-size: 22px;
    color: var(--ink);
  }
  .person-name { color: var(--brand-red); font-weight: 700; }
  .person-title { font-weight: 400; }

  .contacts {
    position: absolute;
    left: 40px;
    top: 340px;
    color: var(--on-dark);
    font-size: 16px;
    line-height: 20px;
    display: grid;
    grid-template-columns: auto auto;
    column-gap: 22px;
    row-gap: 8px;
  }
  .contact { display: flex; align-items: center; gap: 8px; white-space: nowrap; }
  .contact svg { width: 17px; height: 17px; flex: none; }

  .back-mark {
    position: absolute;
    right: 150px;
    top: 52px;
    width: 120px; height: 120px;
    border-radius: 50%;
    background: var(--card-white);
  }
  .tagline {
    position: absolute;
    left: 70px;
    top: 205px;
    color: var(--on-dark);
    font-size: 22px;
    line-height: 1.4;
  }
  .back-web {
    margin-top: 10px;
    font-size: 17px;
    letter-spacing: 4px;
  }
  .back-web strong { font-weight: 700; }
</style>
</head>
<body>

<section class="card card--front">
  <svg class="front-bands" viewBox="0 0 700 400" preserveAspectRatio="none" aria-hidden="true">
    <path d="M0,150 C220,215 470,320 700,338 L700,400 L0,400 Z" fill="var(--brand-red)"/>
    <path d="M0,164 C220,229 470,334 700,350 L700,400 L0,400 Z" fill="var(--brand-grey)"/>
  </svg>

  <div class="brand">
    <span class="brand-dot"></span>
    <span class="brand-name">meridian systems</span>
  </div>

  <p class="person"><span class="person-name">Marcus Hollis,</span> <span class="person-title">General Manager</span></p>

  <div class="contacts">
    <span class="contact">
      <svg viewBox="0 0 24 24"><circle cx="12" cy="12" r="11" fill="none" stroke="#fff" stroke-width="2"/><path d="M8 6l2 3-1.5 1.5c.8 2 2.5 3.7 4.5 4.5L14.5 13.5l3 2-1.5 2.5c-5 0-10-5-10-10z" fill="#fff"/></svg>
      07 3900 4410
    </span>
    <span class="contact">
      <svg viewBox="0 0 24 24"><rect x="6" y="2" width="12" height="20" rx="2" fill="none" stroke="#fff" stroke-width="2"/><rect x="9" y="5" width="6" height="8" fill="#fff"/></svg>
      0400 512 377
    </span>
    <span class="contact">
      <svg viewBox="0 0 24 24"><rect x="2" y="5" width="20" height="14" rx="2" fill="#fff"/><path d="M3 6l9 7 9-7" fill="none" stroke="var(--brand-grey)" stroke-width="2"/></svg>
      hollism@meridiansys.com.au
    </span>
    <span class="contact">
      <svg viewBox="0 0 24 24"><circle cx="12" cy="12" r="10" fill="none" stroke="#fff" stroke-width="2"/><ellipse cx="12" cy="12" rx="4" ry="10" fill="none" stroke="#fff" stroke-width="1.5"/><path d="M2 12h20M4 7h16M4 17h16" stroke="#fff" stroke-width="1.5"/></svg>
      www.meridiansys.com.au
    </span>
  </div>
</section>

<section class="card card--back">
  <span class="back-mark"></span>
  <div class="tagline">
    <p>We are an IT company specializing in Cloud Services</p>
    <p>IT Managed Services, software and hardware</p>
    <p class="back-web">www.<strong>meridiansys</strong>.com.au</p>
  </div>
</section>

</body>
</html>
```